Business card design for my company.
I would like the card's background colour to be black. You can also see our web site to get an idea of our brand. https://www.tmwhomecrafting.com.au/
- Name
- Email

```html
<!DOCTYPE html>
<html lang="en">
<head>
<meta charset="utf-8">
<title>TMW Home Crafting – Business Card</title>
<link href="https://fonts.googleapis.com/css2?family=Montserrat:wght@400;500;700&display=swap" rel="stylesheet">
<style>
  :root {
    --backdrop: #5b5b5b;
    --card-black: #222222;
    --card-black-deep: #1d1d1d;
    --brand-green: #16994a;
    --text-white: #ffffff;
    --emboss: #2c2c2c;
  }
  * { margin: 0; padding: 0; box-sizing: border-box; }
  html, body {
    width: 1200px;
    height: 875px;
    overflow: hidden;
    background: var(--backdrop);
    font-family: "Montserrat", Arial, sans-serif;
  }
  .sheet {
    width: 1200px;
    height: 875px;
    display: flex;
    flex-direction: column;
    align-items: center;
    justify-content: center;
    gap: 56px;
  }
  .card {
    position: relative;
    width: 560px;
    height: 320px;
    border-radius: 20px;
    overflow: hidden;
    background: var(--card-black);
    box-shadow: 0 10px 24px rgba(0,0,0,0.35);
  }

  /* Back of card */
  .card--back { background: var(--card-black-deep); }
  .card--back .brand-name {
    position: absolute;
    left: 0; right: 0; top: 50%;
    transform: translateY(-50%);
    text-align: center;
    font-weight: 700;
    font-size: 44px;
    letter-spacing: 4px;
    color: var(--emboss);
    text-transform: uppercase;
  }

  /* Front of card */
  .accent-band {
    position: absolute;
    inset: 0;
    width: 560px;
    height: 320px;
  }
  .card--front .brand-name {
    position: absolute;
    left: 44px;
    top: 122px;
    width: 210px;
    font-weight: 700;
    font-size: 24px;
    line-height: 1.2;
    letter-spacing: 2px;
    color: var(--text-white);
    text-transform: uppercase;
  }
  .contact {
    position: absolute;
    right: 34px;
    top: 96px;
    text-align: right;
    color: var(--text-white);
  }
  .contact__name {
    font-weight: 700;
    font-size: 21px;
    letter-spacing: 1px;
    text-transform: uppercase;
  }
  .contact__role {
    font-weight: 400;
    font-size: 13px;
    margin-bottom: 16px;
  }
  .contact__line {
    display: flex;
    justify-content: flex-end;
    align-items: center;
    gap: 8px;
    font-size: 12.5px;
    font-weight: 400;
    line-height: 1.75;
  }
  .contact__icon { width: 11px; height: 11px; flex: none; }
</style>
</head>
<body>
<main class="sheet">

  <section class="card card--back" aria-label="Business card back">
    <p class="brand-name">TMW Home Crafting</p>
  </section>

  <section class="card card--front" aria-label="Business card front">
    <svg class="accent-band" viewBox="0 0 560 320" aria-hidden="true">
      <polygon points="345,58 560,42 560,320 100,320" fill="var(--brand-green)"/>
    </svg>

    <p class="brand-name">TMW Home Crafting</p>

    <div class="contact">
      <p class="contact__name">Jonah Reeve</p>
      <p class="contact__role">CEO/Founder</p>
      <p class="contact__line">897-555-0142
        <svg class="contact__icon" viewBox="0 0 24 24" aria-hidden="true"><path fill="#fff" d="M6.6 10.8a15.1 15.1 0 0 0 6.6 6.6l2.2-2.2a1 1 0 0 1 1-.25 11.4 11.4 0 0 0 3.6.6 1 1 0 0 1 1 1V20a1 1 0 0 1-1 1A17 17 0 0 1 3 4a1 1 0 0 1 1-1h3.5a1 1 0 0 1 1 1 11.4 11.4 0 0 0 .6 3.6 1 1 0 0 1-.25 1z"/></svg>
      </p>
      <p class="contact__line">info@tmwhomecrafting.com.au
        <svg class="contact__icon" viewBox="0 0 24 24" aria-hidden="true"><rect x="2" y="5" width="20" height="14" rx="2" fill="#fff"/><path d="M3 6l9 7 9-7" fill="none" stroke="var(--brand-green)" stroke-width="2"/></svg>
      </p>
      <p class="contact__line">www.tmwhomecrafting.com.au
        <svg class="contact__icon" viewBox="0 0 24 24" aria-hidden="true"><g fill="none" stroke="#fff" stroke-width="2"><circle cx="12" cy="12" r="10"/><ellipse cx="12" cy="12" rx="4" ry="10"/><path d="M2 12h20"/></g></svg>
      </p>
    </div>
  </section>

</main>
</body>
</html>
```